Business Card Design - Amberfield Court

We are looking at a new design for our business cards that has a modern and professional look. We run a residential aged care facility focussing on the care of residents. The cards will be used for potential clients, consultants and business opportunities in this sector. Blue and white is our main colours and would to see these colours incorporated in the design.
Industry/Entity Type
Business
Contact Information for Business Card
Amberfield Court, Darren Walsh, dwalsh@amberfieldcourt.com.au, Finance Manager, 0472 639 208, BCom, 37 Marrabel Crescent, Brindle Vale, Qld 4093.
Look and feel
Each slider illustrates characteristics of the customer's brand and the style your logo design should communicate.

```html
<!DOCTYPE html>
<html lang="en">
<head>
<meta charset="utf-8">
<title>Amberfield Court – Business Card</title>
<link rel="stylesheet" href="https://fonts.googleapis.com/css2?family=Open+Sans:wght@400;600;700&family=Oswald:wght@400&display=swap">
<style>
  :root {
    --page-bg: #ececea;
    --card-white: #ffffff;
    --card-dark: #2a2a2a;
    --brand-blue: #4a7a96;
    --brand-taupe: #a99c96;
    --text-dark: #2b2b2b;
    --text-light: #ffffff;
  }
  * { margin: 0; padding: 0; box-sizing: border-box; }
  html, body { width: 1200px; height: 900px; overflow: hidden; }
  body {
    background: var(--page-bg);
    font-family: "Open Sans", Arial, sans-serif;
    position: relative;
  }
  .card {
    position: absolute;
    left: 280px;
    width: 640px;
    height: 391px;
    box-shadow: 0 6px 18px rgba(0,0,0,0.18);
    overflow: hidden;
  }
  .card-back { top: 30px; background: var(--card-dark); }
  .card-front { top: 449px; background: var(--card-white); }
  .card-shapes { position: absolute; inset: 0; }

  .brand-mark {
    position: absolute;
    display: flex;
    align-items: center;
    gap: 16px;
    font-family: "Oswald", "Arial Narrow", sans-serif;
    font-weight: 400;
    letter-spacing: 3px;
    text-transform: uppercase;
    font-size: 30px;
  }
  .brand-dot { width: 30px; height: 30px; border-radius: 50%; flex: none; }
  .card-back .brand-mark { left: 50%; top: 50%; transform: translate(-50%, -50%); color: var(--text-light); font-size: 36px; }
  .card-back .brand-dot { background: var(--text-light); width: 36px; height: 36px; }
  .card-front .brand-mark { right: 34px; top: 168px; color: var(--brand-blue); font-size: 26px; }
  .card-front .brand-dot { background: var(--brand-blue); width: 26px; height: 26px; }

  .holder { position: absolute; left: 46px; top: 14px; }
  .holder-name { color: var(--brand-blue); font-weight: 700; font-size: 21px; line-height: 1.2; }
  .holder-name .credential { font-size: 13px; font-weight: 600; }
  .holder-role { color: var(--text-dark); font-size: 14px; }

  .contact { position: absolute; left: 34px; top: 150px; color: var(--text-dark); font-size: 15px; line-height: 1.4; }
  .address { margin-left: 16px; margin-bottom: 8px; }
  .contact-line { display: flex; align-items: center; gap: 8px; }
  .contact-line svg { width: 12px; height: 12px; fill: var(--brand-blue); flex: none; }
</style>
</head>
<body>
  <section class="card card-back" aria-label="Business card back">
    <div class="brand-mark"><span class="brand-dot"></span>Amberfield Court</div>
  </section>

  <section class="card card-front" aria-label="Business card front">
    <svg class="card-shapes" viewBox="0 0 640 391" aria-hidden="true">
      <polygon points="0,8 32,8 18,26 0,26" fill="var(--brand-taupe)"/>
      <polygon points="0,8 18,8 0,20" fill="var(--brand-blue)"/>
      <polygon points="0,292 300,292 284,316 0,316" fill="var(--brand-blue)"/>
      <polygon points="302,330 640,330 640,364 280,364" fill="var(--brand-taupe)"/>
    </svg>

    <div class="holder">
      <div class="holder-name">Darren Walsh, <span class="credential">BCom</span></div>
      <div class="holder-role">Finance Manager</div>
    </div>

    <div class="contact">
      <div class="address">37 Marrabel Crescent,<br>Brindle Vale, Qld 4093</div>
      <div class="contact-line">
        <svg viewBox="0 0 24 24"><path d="M6.6 10.8a15 15 0 0 0 6.6 6.6l2.2-2.2a1 1 0 0 1 1-.25 11.4 11.4 0 0 0 3.6.57 1 1 0 0 1 1 1V20a1 1 0 0 1-1 1A17 17 0 0 1 3 4a1 1 0 0 1 1-1h3.5a1 1 0 0 1 1 1c0 1.25.2 2.45.57 3.6a1 1 0 0 1-.25 1z"/></svg>
        <span>0472 639 208</span>
      </div>
      <div class="contact-line">
        <svg viewBox="0 0 24 24"><path d="M2 5h20v14H2z M2 5l10 8 10-8" /></svg>
        <span>dwalsh@amberfieldcourt.com.au</span>
      </div>
    </div>

    <div class="brand-mark"><span class="brand-dot"></span>Amberfield Court</div>
  </section>
</body>
</html>
```